Create Website for new company called "Verdale Lodge 37"

Verdale Lodge 37 is a new business situated in Southwestern Colorado. We are creating a business that will rent out spaces where clients can grow their own marijuana. Picture a large green house with partitioned spaces that are secured by a lock. Best way to envision this would be to think of a storage business that rents out storage rooms. The difference is that we will be having the units inside a green house ( for growing purposes) Picture a small area that is secured by locks, Picture an area that has the ability to provide state of the art security, cameras etc. We want to focus our efforts on professionals, blue collar workers and end users of marijuana. Our emphasis is in the area of assisting those whom wish to grow their own plants. We want to provide them a safe facility in which to do that. . Keep in mind that we also build custom grow rooms at clients homes and provide a grow pod (lease these) where a small grow unit will be delivered and picked up from our clients whom want to lease a unit for a short amount of time. We have a business card ( just designed) and will send that information to those whom express an interests in this project. We want to be able to sign people up for our services by entering an agreement and signing the agreement while on the internet. We want to provide our services to those whom consume recreational and medical marijuana. This site will need to gather information I.e email addresses so that we can followup with offers. This is a tremendous opportunity for the right designer. We will be creating many more websites as other states come on line and make marijuana legal to consume. Use the business card model for a point of reference of how we envision the concept. That is a business card we just recently printed. The hands and the plant is our logo so far. Open to suggestions. There will be three levels of service. Bronze, Silver, Gold or Platinum. We will also have a retail biz down the road but not at the present time.

Target Market(s)

Ages 21-60

Industry/Entity Type

Medical

Logo Text

Verdale Lodge 37.

Number of Pages Required

5+ page

Requirements
Must have
• Clean appearance not to busy , easily navigable from link to link, page to page. Must have ability down the road to enter into a contractual agreement via the website. Must use our provided logo and example of that is on our business card that will be uploaded here shortly. We would like to have the colors that are on the business card however if you have suggestions or color schemes that you want us to consider that is okay.
Nice to have
• Nice to have a animation of seed to weed and how clients can save a tremendous amount of money growing their own cannabis. Nice to have testimonial page or feedback page. Have a membership component to website,
Should not have
• No flashing lights, etc. Not to busy in terms of animations.

```html
<!DOCTYPE html>
<html lang="en">
<head>
<meta charset="utf-8">
<title>Verdale Lodge 37 – Home</title>
<link rel="stylesheet" href="https://fonts.googleapis.com/css2?family=Open+Sans:wdth,wght@75..100,300..800&display=swap">
<style>
:root{
  --orange:#cf6e1c;
  --green:#2a9c5a;
  --green-dark:#1f7f46;
  --green-text:#1f7a3f;
  --ink:#333333;
  --muted:#9a9a9a;
  --nav-grey:#9c9c9c;
  --rule:#dddddd;
  --panel:#f5f5f5;
  --footer:#2b2b2b;
  --footer-top:#353535;
  --footer-text:#b5b5b5;
  --white:#ffffff;
}
*{margin:0;padding:0;box-sizing:border-box}
html,body{width:1200px;height:1123px;overflow:hidden;background:var(--white)}
body{font-family:"Open Sans",Arial,sans-serif;color:var(--ink)}
.page{position:relative;width:1170px;height:1095px;transform:scale(1.02564,1.02557);transform-origin:0 0}
.abs{position:absolute}
.condensed{font-family:"Open Sans",Arial,sans-serif;font-stretch:75%;font-weight:700;text-transform:uppercase}

/* header */
.brand{left:117px;top:62px;font-size:50px;line-height:56px;color:var(--ink);letter-spacing:0}
.main-nav{left:562px;top:78px;width:492px;height:37px;border-bottom:1px solid var(--rule);display:flex;justify-content:space-between}
.main-nav a{font-family:"Open Sans",Arial,sans-serif;font-stretch:75%;font-weight:600;font-size:19px;color:var(--nav-grey);text-decoration:none;text-transform:uppercase;padding:0 12px;height:37px;line-height:26px}
.main-nav a.active{color:var(--orange);border-bottom:3px solid var(--orange)}
.main-nav a:last-child{padding-right:2px}

/* hero */
.hero-photo{left:114px;top:146px;width:680px;height:434px;background:linear-gradient(120deg,#b89a78 0%,#8aa06a 30%,#5f8f42 55%,#4f8a34 75%,#3d6b2c 100%)}
.hero-arrow{left:114px;top:346px;width:35px;height:35px;background:rgba(40,40,40,.75)}
.welcome{left:794px;top:146px;width:260px;height:434px;background:linear-gradient(160deg,#2fa862 0%,var(--green) 50%,#258f51 100%);color:var(--white);padding:44px 20px 0 21px}
.welcome h1{font-size:44px;line-height:46px;margin-bottom:10px}
.welcome p{font-size:14.5px;line-height:24px}
.btn-light{display:inline-block;margin-top:17px;background:var(--white);color:#666;font-size:13px;padding:0 12px;height:36px;line-height:36px;text-decoration:none}

/* features */
.feature{top:612px;width:324px}
.feature h2{font-size:30px;line-height:32px;color:var(--orange);margin-left:-1px}
.feature-photo{width:323px;height:134px;margin-top:7px}
.feature p{margin-top:10px;font-size:13px;line-height:20px;color:var(--muted);padding-left:1px}
.btn-outline{display:inline-block;margin-top:20px;border:1px solid var(--green);color:var(--green);font-size:14px;height:38px;line-height:36px;padding:0 12px;text-decoration:none}

/* contact panel */
.contact{left:794px;top:580px;width:260px;height:373px;background:var(--panel)}
.contact h2{position:absolute;left:20px;top:32px;font-size:30px;line-height:32px;color:var(--orange)}
.contact-list{position:absolute;left:11px;top:71px;width:238px;list-style:none;border-top:1px solid var(--rule)}
.contact-list li{position:relative;height:69px;border-bottom:1px solid var(--rule);padding:15px 0 0 36px;font-size:14px;line-height:20px}
.contact-list li:last-child{height:73px}
.contact-list svg{position:absolute;left:11px;top:18px}
.contact-name{color:var(--green-text)}
.contact-info{color:var(--ink)}
.social{position:absolute;left:22px;top:297px;display:flex;gap:18px}
.social span{display:block;width:23px;height:23px;border-radius:4px;background:#9a9a9a}
.social span.accent{background:var(--green)}

/* footer */
.site-footer{left:0;top:955px;width:1170px;height:140px;background:linear-gradient(var(--footer-top),var(--footer))}
.footer-nav{position:absolute;left:317px;top:27px;display:flex;gap:0}
.footer-nav a{color:var(--footer-text);font-size:13px;text-decoration:none;margin-right:62px}
.footer-nav a::before{content:"•";font-size:10px;margin-right:4px;position:relative;top:-2px}
.footer-rule{position:absolute;left:106px;top:67px;width:958px;height:1px;background:#444}
.copyright{position:absolute;left:0;top:92px;width:1170px;text-align:center;font-size:13px;font-weight:600;color:#9b9b9b}
</style>
</head>
<body>
<div class="page">

  <header>
    <div class="abs brand condensed">Verdale Lodge 37</div>
    <nav class="abs main-nav">
      <a class="active" href="#">Home</a>
      <a href="#">About us</a>
      <a href="#">Services</a>
      <a href="#">News</a>
      <a href="#">Contact us</a>
    </nav>
  </header>

  <section>
    <div class="abs hero-photo" role="img" aria-label="Greenhouse interior with tall leafy plants and wooden raised beds"></div>
    <div class="abs hero-arrow">
      <svg width="35" height="35" viewBox="0 0 35 35"><path d="M25 17.5H11M17 11l-6.5 6.5L17 24" stroke="#fff" stroke-width="3" fill="none" stroke-linecap="round" stroke-linejoin="round"/></svg>
    </div>
    <div class="abs welcome">
      <h1 class="condensed">Welcome</h1>
      <p>Suspendisse vulputate semper ante, et consequat magna consec-tetur in. Etiam lorem dolor, elementum et euismod nec, imperdiet quis sapien. Curabitur euismod molestie magna eget congue. Fusce fringilla purus id hendrerit sagittis. Maecenas eros massa, laoreet quis tellus eget.</p>
      <a class="btn-light" href="#">Read more</a>
    </div>
  </section>

  <section>
    <article class="abs feature" style="left:116px">
      <h2 class="condensed">Indoor growing</h2>
      <div class="feature-photo" role="img" aria-label="Dense indoor plants under grow lights" style="background:linear-gradient(180deg,#6b7560 0%,#5c7a3e 45%,#4d6a32 100%)"></div>
      <p>Mauris ut consectetur nisi. Proin in ante et orci mollis semper. Nullam a lacus in lorem consequat pretium. Quisque scelerisque, justo sit urna id neque.</p>
      <a class="btn-outline" href="#">BOOK NOW</a>
    </article>
    <article class="abs feature" style="left:457px">
      <h2 class="condensed">Outdoor growing</h2>
      <div class="feature-photo" role="img" aria-label="Close view of green leaves outdoors" style="background:linear-gradient(90deg,#b9c6a8 0%,#7fa85a 40%,#5e9a3c 70%,#8bb36a 100%)"></div>
      <p>Mauris ut consectetur nisi. Proin in ante et orci mollis semper. Nullam a lacus in lorem consequat pretium. Quisque scelerisque, justo sit urna id neque.</p>
      <a class="btn-outline" href="#">BOOK NOW</a>
    </article>

    <aside class="abs contact">
      <h2 class="condensed">Contact us</h2>
      <ul class="contact-list">
        <li>
          <svg width="13" height="20" viewBox="0 0 13 20"><rect x="1" y="1" width="11" height="18" rx="2" fill="none" stroke="#2a9c5a" stroke-width="2"/><rect x="3.5" y="4" width="6" height="9" fill="#2a9c5a"/><circle cx="6.5" cy="16" r="1.2" fill="#2a9c5a"/></svg>
          <div class="contact-name">Jonah Pellister</div>
          <div class="contact-info">Cell 555.014.2276</div>
        </li>
        <li>
          <svg width="13" height="20" viewBox="0 0 13 20"><rect x="1" y="1" width="11" height="18" rx="2" fill="none" stroke="#2a9c5a" stroke-width="2"/><rect x="3.5" y="4" width="6" height="9" fill="#2a9c5a"/><circle cx="6.5" cy="16" r="1.2" fill="#2a9c5a"/></svg>
          <div class="contact-name">Curtis Navarre</div>
          <div class="contact-info">Cell 555.019.4830</div>
        </li>
        <li>
          <svg width="15" height="12" viewBox="0 0 15 12" style="top:20px;left:10px"><rect x="0" y="1" width="15" height="11" fill="#2a9c5a"/><path d="M0 1.5l7.5 5.5 7.5-5.5" stroke="#f5f5f5" stroke-width="1.5" fill="none"/></svg>
          <div class="contact-name">Dale Ormsby</div>
          <div class="contact-info">Dale@VerdaleLodge37.com</div>
        </li>
      </ul>
      <div class="social">
        <span class="accent"></span>
        <span></span>
        <svg width="26" height="20" viewBox="0 0 26 20"><rect x="0" y="1" width="26" height="18" rx="2" fill="#9a9a9a"/><path d="M1 3l12 8 12-8" stroke="#f5f5f5" stroke-width="2" fill="none"/></svg>
      </div>
    </aside>
  </section>

  <footer class="abs site-footer">
    <nav class="footer-nav">
      <a href="#">Home</a>
      <a href="#">About us</a>
      <a href="#">Services</a>
      <a href="#">News</a>
      <a href="#">Contact us</a>
    </nav>
    <div class="footer-rule"></div>
    <p class="copyright">Copyright &nbsp;©&nbsp; 2014 &nbsp;Verdale Lodge 37. &nbsp; All rights reserved.</p>
  </footer>

</div>
</body>
</html>
```